business card - Helicopter Flight Services, Flight School, etc.

We need a business card design for a new helicopter service.

We offer Helicopter Flight Services, Aerial Filming & Photography, Flight School, and Helicopter Tours. In that order.

Summit BladeAir, Inc.
Dennis Tollerby
SummitBladeair@Kestmail.com
626-418-7352

Based at the Brenwick Airport in Van Nuys, CA. The final design should communicate integrity and safety. Pictures or logos at your discretion.

Card back side - surprise me.

```html
<!DOCTYPE html>
<html lang="en">
<head>
<meta charset="utf-8">
<title>Summit BladeAir, Inc. — Business Card</title>
<link href="https://fonts.googleapis.com/css2?family=Arimo:wght@400;700&family=Open+Sans:wght@400;600&display=swap" rel="stylesheet">
<style>
  :root {
    --page: #e9e7e3;
    --card-black: #060607;
    --card-sheen: #1c1c1f;
    --band-light: #e6e7ea;
    --lavender: #8f97d6;
    --ink-dark: #141821;
    --text-light: #f4f4f6;
    --text-soft: #c9c9cf;
    --sky: #dfe6ea;
    --meadow: #6f9a3f;
    --meadow-deep: #4d7a2c;
  }
  * { margin: 0; padding: 0; box-sizing: border-box; }
  html, body { width: 1200px; height: 892px; overflow: hidden; background: var(--page); }
  .sheet { position: relative; width: 1200px; height: 892px; }
  .card {
    position: absolute; left: 290px; width: 620px; height: 354px;
    background: linear-gradient(160deg, var(--card-sheen) 0%, var(--card-black) 45%, var(--card-black) 100%);
    box-shadow: 0 10px 30px rgba(0,0,0,.28);
    overflow: hidden;
  }
  .card--front { top: 62px; }
  .card--back { top: 476px; }
  .front-art { position: absolute; inset: 0; }
  .company-band {
    position: absolute; left: 196px; top: 38px; width: 424px; height: 60px;
    background: rgba(232,233,237,.86);
    display: flex; align-items: center; padding-left: 20px;
    font-family: "Arimo", Arial, sans-serif; font-size: 33px; color: var(--ink-dark);
    letter-spacing: .3px; white-space: nowrap;
  }
  .person-name {
    position: absolute; right: 48px; top: 170px;
    font-family: "Open Sans", Arial, sans-serif; font-size: 28px; line-height: 40px; color: var(--lavender);
  }
  .contact-list {
    position: absolute; right: 22px; top: 220px; list-style: none;
    font-family: "Open Sans", Arial, sans-serif; font-size: 17px; color: var(--text-light);
    text-align: right; line-height: 27px;
  }
  .contact-list li { display: flex; justify-content: flex-end; align-items: center; gap: 10px; }
  .contact-list .no-icon { padding-right: 26px; }
  .contact-icon { width: 16px; height: 16px; flex: none; }
  .back-name {
    position: absolute; left: 0; right: 0; top: 118px; text-align: center;
    font-family: "Arimo", Arial, sans-serif; font-size: 50px; font-weight: 400; color: var(--text-light);
    letter-spacing: 1px;
  }
  .back-services {
    position: absolute; left: 0; right: 0; top: 192px; text-align: center;
    font-family: "Open Sans", Arial, sans-serif; font-size: 18px; line-height: 28px; color: var(--text-soft);
    letter-spacing: .3px;
  }
  .back-services span { display: block; }
</style>
</head>
<body>
<main class="sheet">
  <section class="card card--front" aria-label="Business card front">
    <svg class="front-art" width="620" height="354" viewBox="0 0 620 354">
      <defs>
        <linearGradient id="upperLight" x1="0" y1="0" x2="1" y2="1">
          <stop offset="0" stop-color="#ffffff"/>
          <stop offset="1" stop-color="#cfd2d8"/>
        </linearGradient>
        <linearGradient id="photoTone" x1="0" y1="0" x2="0" y2="1">
          <stop offset="0" stop-color="var(--sky)"/>
          <stop offset=".35" stop-color="#9db58a"/>
          <stop offset=".6" stop-color="var(--meadow)"/>
          <stop offset="1" stop-color="var(--meadow-deep)"/>
        </linearGradient>
        <clipPath id="upperArea">
          <path d="M0 0 H620 V40 Q430 190 0 188 Z"/>
        </clipPath>
      </defs>
      <path d="M0 0 H620 V52 Q430 204 0 202 Z" fill="var(--lavender)"/>
      <g clip-path="url(#upperArea)">
        <rect x="0" y="0" width="620" height="210" fill="url(#upperLight)"/>
        <rect x="0" y="0" width="450" height="210" fill="url(#photoTone)" role="img" aria-label="Photo of a helicopter parked on a grassy field"/>
      </g>
    </svg>
    <div class="company-band">Summit BladeAir, Inc.</div>
    <p class="person-name">Dennis Tollerby</p>
    <ul class="contact-list">
      <li>626-418-7352
        <svg class="contact-icon" viewBox="0 0 16 16" aria-hidden="true"><rect width="16" height="16" fill="#fff"/><path d="M5 3 L7 3 L7.6 6 L6.4 7 Q7.4 9 9 9.6 L10 8.4 L13 9 L13 11 Q12.5 13 10.5 12.6 Q4.5 11 3.4 5.5 Q3.2 3.4 5 3 Z" fill="#111"/></svg>
      </li>
      <li>SummitBladeair@Kestmail.com
        <svg class="contact-icon" viewBox="0 0 16 16" aria-hidden="true"><rect width="16" height="16" fill="#fff"/><rect x="3" y="4.5" width="10" height="7" fill="none" stroke="#111" stroke-width="1.3"/><path d="M3 4.5 L8 8.5 L13 4.5" fill="none" stroke="#111" stroke-width="1.3"/></svg>
      </li>
      <li>2740 W. Larkmoor Ave. Ste.B
        <svg class="contact-icon" viewBox="0 0 16 16" aria-hidden="true"><rect width="16" height="16" fill="#fff"/><path d="M8 13.5 Q4 9 4 6.5 A4 4 0 0 1 12 6.5 Q12 9 8 13.5 Z" fill="#111"/><circle cx="8" cy="6.5" r="1.5" fill="#fff"/></svg>
      </li>
      <li class="no-icon">Van Nuys, CA 91406</li>
    </ul>
  </section>

  <section class="card card--back" aria-label="Business card back">
    <h1 class="back-name">Summit BladeAir</h1>
    <p class="back-services">
      <span>Helicopter Flight Services · Aerial Filming &amp; Photography</span>
      <span>Flight School · Helicopter Tours</span>
    </p>
  </section>
</main>
</body>
</html>
```